Specialist Recruitment Process Outsourcing (RPO) company needs a modern, sleek website

We need a website which showcases our service offering, describes our onshore and offshore options. Our service is basically building teams of recruiters who become the outsourced (but in-house) recruiter for that specific client. Our logo colours include a light, bright green and a dark/midnight blue. This company will be targeting companies who need help with recruitment in technology, finance, engineering and other white collar industries. We are looking for a look and feeling that communicates cutting edge technology with a bright, energetic appeal. I will include some logo design files to work with.

Target Market(s)

Businesses: start ups who need to grow their staff, SMEs with regular recruitment needs, and larger businesses

Industry/Entity Type

Recruitment

Coding

Coded - Design and coding required

Number of Pages Required

4 page

Font styles to use
Sans Serif

Requirements
Must have
• Landing page should be highly visual, either with dynamic image or scrolling stills accompanies by our core service offering, values, and benefits.

A Services page will allows more detail about what we do, with a call to action.

A User Stories page will showcase some examples of how our services will help certain types of businesses.

Onshore/Offshore page will breakdown the benefits of both approaches and how combinations can work well.

Should fit the colour theming of our logo (files uploaded).

Nice to have
• Imagery can be both around business and people. We are looking for more of a "startup" feel than a corporate-y feel.

```html
<!DOCTYPE html>
<html lang="en">
<head>
<meta charset="utf-8">
<title>Hirewave — Specialist RPO</title>
<link href="https://fonts.googleapis.com/css2?family=Montserrat:wght@400;500;700;800&display=swap" rel="stylesheet">
<style>
:root{
  --navy:#0a0c2e;
  --navy-soft:#1b2150;
  --green:#22e08a;
  --white:#ffffff;
  --text:#2a2a3a;
}
*{margin:0;padding:0;box-sizing:border-box}
html,body{width:1200px;height:2830px;overflow:hidden;background:var(--white)}
body{position:relative;font-family:'Montserrat',sans-serif;color:var(--text)}
.abs{position:absolute}

.site-header{left:0;top:0;width:1200px;height:126px;background:var(--navy)}
.brand{display:flex;flex-direction:column;align-items:center;gap:12px}
.brand-mark{width:30px;height:30px;border-radius:50%;background:var(--green)}
.brand-name{font-weight:500;font-size:15px;letter-spacing:4px;color:var(--green)}
.nav{display:flex;gap:0;font-size:16px;color:var(--white)}
.nav a{position:absolute;color:var(--white);text-decoration:none;white-space:nowrap}
.nav a.active{color:var(--green)}
.nav-underline{left:618px;top:123px;width:55px;height:4px;background:var(--green)}

.hero{left:0;top:126px;width:1200px;height:632px}
.hero-title{left:0;top:350px;width:1200px;text-align:center;color:var(--white);font-weight:700;font-size:37px;line-height:43px;text-shadow:0 2px 8px rgba(0,0,0,.35)}
.btn{display:flex;align-items:center;justify-content:center;background:var(--navy);color:var(--green);font-size:14.5px;width:129px;height:38px;text-decoration:none}
.slider-dots span{position:absolute;left:0;width:10px;height:10px;border-radius:50%;background:var(--white)}
.slider-dots span.on{background:var(--green)}

.eyebrow{font-weight:700;font-size:24px;color:var(--navy)}
.section-title{font-weight:700;font-size:37px;color:var(--green)}
.heading{font-weight:700;font-size:38px;color:var(--navy)}
.copy{font-size:13.4px;line-height:25.7px;color:var(--text)}
.photo{border:0}
.frame{border:4px solid var(--green)}

.service-tab-label{left:468px;top:1269px;width:255px;height:52px;display:flex;align-items:center;justify-content:center;font-weight:700;font-size:38px;color:var(--navy)}
.service-title{font-weight:700;font-size:37px;color:var(--white)}
.service-copy{font-size:13.4px;line-height:25.7px;color:var(--white)}

.site-footer{left:0;top:2630px;width:1200px;height:200px;background:var(--navy)}
.social{display:flex;gap:16px}
.social span{width:14px;height:14px;border-radius:50%;background:var(--white)}
.copyright{font-size:13px;color:var(--white)}
</style>
</head>
<body>

<header class="abs site-header">
  <div class="abs brand" style="left:110px;top:22px;width:143px">
    <span class="brand-mark"></span>
    <span class="brand-name">HIREWAVE</span>
  </div>
  <nav class="nav">
    <a class="active" style="left:621px;top:50px">Home</a>
    <a style="left:704px;top:50px">About Us</a>
    <a style="left:813px;top:50px">Services</a>
    <a style="left:912px;top:50px">Stories</a>
    <a style="left:1004px;top:50px">Contact Us</a>
  </nav>
  <div class="abs nav-underline"></div>
</header>

<section class="abs hero">
  <svg width="1200" height="632" viewBox="0 0 1200 632" style="position:absolute;left:0;top:0">
    <defs>
      <linearGradient id="heroFill" x1="0" y1="0" x2="1" y2="0.4">
        <stop offset="0" stop-color="#6e6a62"/>
        <stop offset="0.35" stop-color="#9b8a7e"/>
        <stop offset="0.55" stop-color="#b9c3cf"/>
        <stop offset="0.8" stop-color="#8c6b5e"/>
        <stop offset="1" stop-color="#d9dde0"/>
      </linearGradient>
    </defs>
    <polygon points="0,0 1200,0 1200,484 599,630 0,484" fill="url(#heroFill)" role="img" aria-label="Smiling woman in a bright office with colleagues talking in the background"/>
    <polyline points="0,488 599,627 1200,488" fill="none" stroke="#22e08a" stroke-width="7"/>
  </svg>
</section>
<h1 class="abs hero-title">We are a Specialist Recruitment<br>Process Outsourcing (RPO) company.</h1>
<a class="abs btn" style="left:535px;top:463px">READ MORE</a>
<div class="abs slider-dots" style="left:1073px;top:453px">
  <span style="top:0"></span><span class="on" style="top:18px"></span><span style="top:36px"></span><span style="top:54px"></span>
</div>

<section class="about">
  <div class="abs eyebrow" style="left:110px;top:830px">About</div>
  <h2 class="abs section-title" style="left:110px;top:862px">Hirewave</h2>
  <p class="abs copy" style="left:114px;top:920px;width:462px">Sed ut perspiciatis unde omnis iste natus error sit voluptatem accusantium doloremque laudantium, totam rem aperiam, eaque ipsa quae ab illo inventore veritatis et quasi architecto beatae vitae dicta sunt explicabo. Nemo enim ipsam voluptatem quia voluptas sit aspernatur aut odit aut fugit, sed quia consequuntur magni dolores eos qui ratione voluptatem sequi nesciunt.</p>
  <a class="abs btn" style="left:115px;top:1095px">READ MORE</a>
  <div class="abs photo" style="left:614px;top:831px;width:478px;height:321px;background:linear-gradient(120deg,#d8d6cf,#a9a69c 45%,#6f6a62 75%,#c9c7c2)" role="img" aria-label="Smiling woman in glasses shaking hands across a desk"></div>
  <div class="abs frame" style="left:598px;top:813px;width:476px;height:319px"></div>
</section>

<section class="services">
  <svg class="abs" style="left:0;top:1269px" width="1200" height="508" viewBox="0 0 1200 508">
    <defs>
      <linearGradient id="onshoreFill" x1="0" y1="0" x2="1" y2="1">
        <stop offset="0" stop-color="#3a4674"/>
        <stop offset="1" stop-color="#1f2650"/>
      </linearGradient>
      <linearGradient id="offshoreFill" x1="0" y1="0" x2="1" y2="0">
        <stop offset="0" stop-color="#4c4a52"/>
        <stop offset="0.5" stop-color="#8c8f98"/>
        <stop offset="1" stop-color="#2f6aa8"/>
      </linearGradient>
    </defs>
    <polygon points="468,0 692,0 723,52 495,52" fill="#22e08a"/>
    <polygon points="0,52 599,52 599,506 0,407" fill="url(#onshoreFill)" role="img" aria-label="Business team meeting around a table"/>
    <polygon points="599,52 1200,52 1200,411 599,506" fill="url(#offshoreFill)" role="img" aria-label="Two women reviewing a laptop by an office window"/>
  </svg>
  <div class="abs service-tab-label">Service</div>
  <h3 class="abs service-title" style="left:110px;top:1437px">onshore</h3>
  <p class="abs service-copy" style="left:114px;top:1484px;width:410px">Sed ut perspiciatis unde omnis iste natus error sit voluptatem accusantium doloremque laudantium, totam rem aperiam, eaque ipsa quae ab illo inventore veritatis et quasi architecto beatae vitae dicta sunt explicabo.</p>
  <a class="abs btn" style="left:115px;top:1602px">READ MORE</a>
  <h3 class="abs service-title" style="left:654px;top:1653px">offshore</h3>
</section>

<section class="values">
  <div class="abs frame" style="left:126px;top:1854px;width:476px;height:320px"></div>
  <div class="abs photo" style="left:110px;top:1868px;width:478px;height:322px;background:linear-gradient(110deg,#e9ecef,#c7cdd4 40%,#3b4766 70%,#d5d8db)" role="img" aria-label="Two businessmen shaking hands in a meeting room with colleagues seated"></div>
  <h2 class="abs heading" style="left:639px;top:1866px">Our Values</h2>
  <p class="abs copy" style="left:640px;top:1947px;width:462px">Sed ut perspiciatis unde omnis iste natus error sit voluptatem accusantium doloremque laudantium, totam rem aperiam, eaque ipsa quae ab illo inventore veritatis et quasi architecto beatae vitae dicta sunt explicabo. Nemo enim ipsam voluptatem quia voluptas sit aspernatur aut odit aut fugit, sed quia consequuntur magni dolores eos qui ratione voluptatem sequi nesciunt.</p>
  <a class="abs btn" style="left:641px;top:2121px">READ MORE</a>
</section>

<section class="benefits">
  <h2 class="abs heading" style="left:107px;top:2260px">Our Benefits</h2>
  <p class="abs copy" style="left:110px;top:2340px;width:462px">Sed ut perspiciatis unde omnis iste natus error sit voluptatem accusantium doloremque laudantium, totam rem aperiam, eaque ipsa quae ab illo inventore veritatis et quasi architecto beatae vitae dicta sunt explicabo. Nemo enim ipsam voluptatem quia voluptas sit aspernatur aut odit aut fugit, sed quia consequuntur magni dolores eos qui ratione voluptatem sequi nesciunt.</p>
  <a class="abs btn" style="left:110px;top:2515px">READ MORE</a>
  <div class="abs frame" style="left:602px;top:2228px;width:477px;height:320px"></div>
  <div class="abs photo" style="left:618px;top:2242px;width:477px;height:321px;background:linear-gradient(100deg,#3c3a38,#6b5a4a 45%,#e6e4e1 75%,#8a7d70)" role="img" aria-label="Excited young man celebrating at an office table with a colleague"></div>
</section>

<footer class="abs site-footer">
  <div class="abs brand" style="left:107px;top:45px;width:143px">
    <span class="brand-mark"></span>
    <span class="brand-name">HIREWAVE</span>
  </div>
  <nav class="nav">
    <a class="active" style="left:615px;top:58px">Home</a>
    <a style="left:700px;top:58px">About Us</a>
    <a style="left:808px;top:58px">Services</a>
    <a style="left:908px;top:58px">Stories</a>
    <a style="left:1000px;top:58px">Contact Us</a>
  </nav>
  <div class="abs social" style="left:1000px;top:103px"><span></span><span></span><span></span></div>
  <div class="abs copyright" style="right:115px;top:138px">© 2020 &nbsp;|&nbsp; www.hirewave-rpo.com</div>
</footer>

</body>
</html>
```